Summer Music/Chorus/Choir Camp for Young Singers Ages 8-13

We need a flyer for a summer camp for young singers ages 8-13. We are nonprofit community children's chorus in Miami, FL. Our camp provides specialized training in music theory, sight-reading,and aural training through daily choral rehearsals in an environment that is both positive and a lot of fun! Our camp offers children the opportunity to come as they are, no matter the level of experience, and grow tremendously in their musicianship skills. In addition to this, our campers participate in song-writing, masterclasses, community performances, and media projects. The final design should be clean, fun, not too crowded, should appeal to boys and girls ages 8-13, and something someone that age would consider "cool" and not too childish. Drawings are cool, something different.
Updates

Target Market(s)

Ages 8-13 and parents of those kids.

Industry/Entity Type

Community

Requirements
Must have
• All info attached.
Nice to have
• Things that relate to music, especially related to singing/choirs
Should not have
• instruments, stock photos of children, or photos from our website (unless they are used very creatively), or photos in general. I've attached our previous camp flyer and our current organization flyer but I don't necessarily want this flyer to look like those.

```html
<!DOCTYPE html>
<html lang="en">
<head>
<meta charset="utf-8">
<title>Summer Camp 2016 – Bright Voices Chorus</title>
<link rel="stylesheet" href="https://fonts.googleapis.com/css2?family=Oswald:wght@500;600&family=Roboto+Condensed:wght@400;700&family=Roboto:ital,wght@0,300;0,400;0,500;1,300&display=swap">
<style>
  :root {
    --paper: #ffffff;
    --crimson: #d81b5c;
    --ink: #2b2b2b;
    --body-ink: #555555;
    --muted: #777777;
    --teal: #4b8c86;
    --note-top: #62cbe0;
    --note-bottom: #2f9cb3;
    --pin: #3fa44a;
    --badge: #3a3a3a;
  }
  * { box-sizing: border-box; margin: 0; padding: 0; }
  html, body { width: 966px; height: 1200px; overflow: hidden; background: var(--paper); }
  .flyer { position: relative; width: 966px; height: 1200px; overflow: hidden; background: var(--paper); font-family: "Roboto", sans-serif; }

  .sound-band {
    position: absolute; left: 0; top: 40px; width: 966px; height: 430px;
    background:
      linear-gradient(180deg, rgba(255,255,255,0) 0%, rgba(255,255,255,0) 70%, #fff 100%),
      linear-gradient(90deg, #f6b0a4 0%, #fbe0a8 22%, #e4efbd 40%, #d8ecd6 55%, #e6e6f3 72%, #efc2d4 88%, #c9dcee 100%);
    opacity: .75;
  }

  .headline {
    position: absolute; left: 0; top: 150px; width: 966px; text-align: center;
    font-family: "Oswald", sans-serif; font-weight: 600; font-size: 108px; line-height: 1;
    letter-spacing: -3px; color: var(--crimson);
    -webkit-text-stroke: 0; text-shadow: 0 0 4px #fff, 0 0 4px #fff, 0 0 6px #fff;
  }
  .tagline {
    position: absolute; left: 0; top: 278px; width: 966px; text-align: center;
    font-family: "Oswald", sans-serif; font-weight: 500; font-size: 44px; line-height: 1;
    letter-spacing: -1px; color: var(--ink);
  }
  .tagline .star { font-size: 34px; vertical-align: 4px; margin: 0 4px; }

  .chorus-name {
    position: absolute; left: 30px; top: 590px; width: 420px;
    font-family: "Roboto", sans-serif; font-weight: 400; font-size: 58px; line-height: 1.05;
    color: var(--teal); display: flex; align-items: center; gap: 16px;
  }
  .chorus-name .mark { width: 34px; height: 34px; border-radius: 50%; background: var(--teal); flex: none; }

  .intro {
    position: absolute; left: 51px; top: 806px; width: 400px;
    font-weight: 300; font-size: 17.3px; line-height: 24.4px; color: var(--body-ink);
    text-align: justify; hyphens: auto;
  }
  .nonprofit-note {
    position: absolute; left: 20px; top: 1090px; width: 460px; text-align: center;
    font-style: italic; font-weight: 300; font-size: 14.5px; line-height: 17px; color: var(--muted);
  }

  .details-note {
    position: absolute; left: 525px; top: 538px; width: 395px; height: 380px;
    background: linear-gradient(180deg, var(--note-top) 0%, var(--note-top) 55%, var(--note-bottom) 100%);
    transform: rotate(-4deg);
    box-shadow: 0 14px 22px rgba(0,0,0,.18);
    color: #fff; font-family: "Roboto Condensed", sans-serif; text-align: center;
    padding-top: 118px;
  }
  .details-note .dates { font-weight: 700; font-size: 30px; line-height: 1.1; }
  .details-note .extended { font-weight: 700; font-size: 16.5px; line-height: 23px; margin-top: 8px; }
  .details-note .venue { font-weight: 700; font-size: 20.5px; line-height: 25px; margin-top: 30px; }

  .pushpin { position: absolute; left: 700px; top: 500px; width: 50px; height: 80px; }

  .phone {
    position: absolute; left: 570px; top: 966px; display: flex; align-items: center; gap: 16px;
    font-weight: 500; font-size: 41px; color: var(--ink); letter-spacing: 1px;
  }
  .phone svg { width: 44px; height: 44px; }
  .web-contact {
    position: absolute; left: 520px; top: 1022px; width: 400px; text-align: center;
    font-weight: 400; font-size: 21px; line-height: 24px; color: var(--ink);
  }

  .partners { position: absolute; left: 486px; top: 1152px; display: flex; align-items: center; gap: 10px; }
  .partners .badge-county { width: 98px; height: 44px; border-radius: 4px 22px 22px 4px; background: var(--badge); }
  .partners .badge-culture { width: 52px; height: 52px; border: 3px solid var(--badge); }
  .partners .badge-foundation { width: 250px; height: 30px; background: var(--badge); margin-left: 8px; }
</style>
</head>
<body>
<main class="flyer">
  <div class="sound-band" role="img" aria-label="Colourful pixel-style sound equalizer pattern in soft rainbow tones"></div>

  <h1 class="headline">SUMMER CAMP 2016</h1>
  <p class="tagline">MUSIC<span class="star">★</span>CHORUS<span class="star">★</span>CHOIR</p>

  <div class="chorus-name"><span class="mark"></span><span>Bright Voices Chorus</span></div>

  <p class="intro">Youth and children who love to sing will have a blast at our choral camp! Our music educators and industry professionals are dedicated to enhancing the lives of young singers through choral training which develops vocal technique, ear-training, music reading, and interpersonal skills. Activities are fun and interactive and former music training is not necessary. Singers in grades 3-9 are invited to attend! Register today!</p>

  <p class="nonprofit-note">Bright Voices Chorus is a 501 (c)(3) Nonprofit organization.<br>Donations made to BVC are tax-exempt</p>

  <section class="details-note">
    <p class="dates">July 18-29, 9am-3pm (M-F)*</p>
    <p class="extended">*Extended hours available (7:30am-5:30pm)<br>for an extra $50 per week.</p>
    <p class="venue">Southbay Community Arts Hall,<br>4820 Coral Palm Avenue<br>Miami, FL 33100</p>
  </section>

  <svg class="pushpin" viewBox="0 0 50 80" aria-hidden="true">
    <line x1="25" y1="50" x2="26" y2="78" stroke="#8a6a4a" stroke-width="3"/>
    <rect x="17" y="22" width="16" height="28" rx="6" fill="var(--pin)"/>
    <ellipse cx="25" cy="50" rx="14" ry="6" fill="#2f8a3a"/>
    <circle cx="25" cy="16" r="14" fill="var(--pin)"/>
    <circle cx="20" cy="11" r="4" fill="#9be0a0"/>
  </svg>

  <div class="phone">
    <svg viewBox="0 0 44 44" aria-hidden="true">
      <circle cx="22" cy="22" r="19.5" fill="none" stroke="var(--ink)" stroke-width="3"/>
      <path d="M15 11c1.5-1 3-.5 3.6.8l1.8 4c.4 1-.1 2-.9 2.6l-1.5 1.1c1 2.6 3 4.8 5.6 6.1l1.2-1.4c.7-.8 1.8-1 2.7-.5l3.8 2c1.2.7 1.5 2.2.6 3.5-1.8 2.6-4.6 3.4-7.6 2-6.2-2.9-10.4-8.1-12-13.5-.9-3 .2-5.6 2.7-6.7z" fill="var(--ink)"/>
    </svg>
    <span>555.014.2290</span>
  </div>
  <p class="web-contact">hello@brightvoiceschorus.org<br>brightvoiceschorus.org</p>

  <div class="partners">
    <div class="badge-county" role="img" aria-label="County partner badge"></div>
    <div class="badge-culture" role="img" aria-label="Cultural program partner badge"></div>
    <div class="badge-foundation" role="img" aria-label="Foundation partner badge"></div>
  </div>
</main>
</body>
</html>
```